Food Hall in Seabrook, CA by the Pacific Ocean that has 15 vendors and 2 bars

We need a web page design that highlights our food hall in Seabrook, CA. The name of the food hall is Calloway Food Hall. Inside of the food hall there are 15 different vendors and 2 bars. The place has a beautiful patio and it is by Pacific Ocean. Most of the vendors are local to San Clemente area. The highly anticipated location is opening during the summer of 2025. Website should have a dropdown menu for the different vendors that are in the food hall and people should be able to click to their respective business website. The website should also include link to our social media channels and also a link to provide comments and subscribe for the mailing list.
Target Market(s)
Mostly residents in the Seabrook, CA and surrounding areas. Couples, families and tourist alike that are looking for an exceptional dining experience that everyone can find something they like.
Industry/Entity Type
Restaurants
Coding
Number of Pages Required
Font styles to use
Look and feel

```html
<!DOCTYPE html>
<html lang="en">
<head>
<meta charset="utf-8">
<title>Calloway Food Hall – Coastal Dining</title>
<link rel="stylesheet" href="https://fonts.googleapis.com/css2?family=Montserrat:wght@400;500;600;700&display=swap">
<style>
:root{
  --blue:#1d4f9c;
  --blue-soft:#6e9fcf;
  --blue-pill:#6f9fd0;
  --ink:#111;
  --muted:#555;
  --star:#f5a623;
  --white:#fff;
}
*{box-sizing:border-box;margin:0;padding:0}
html,body{width:1200px;height:3113px;overflow:hidden}
body{font-family:'Montserrat',sans-serif;color:var(--ink);background:var(--white);position:relative}
a{color:inherit;text-decoration:none}

.top-strip{height:10px;background:var(--blue)}
.site-header{height:87px;display:flex;align-items:center;justify-content:space-between;padding:0 110px}
.brand{font-size:25px;font-weight:600;color:var(--blue)}
.main-nav{display:flex;gap:34px;font-size:15px;color:#333}
.main-nav .active{color:var(--blue);font-weight:600}
.main-nav .has-drop::after{content:"";display:inline-block;width:6px;height:6px;border-right:2px solid #333;border-bottom:2px solid #333;transform:rotate(45deg);margin-left:7px;position:relative;top:-3px}

.hero{position:relative;height:508px;overflow:hidden}
.hero-photo{position:absolute;inset:0;background:linear-gradient(100deg,#d9d2c4 0%,#b98b5c 30%,#e6ddd0 45%,#6b5a45 70%,#2a2a2a 100%)}
.hero-badge{position:absolute;left:666px;top:43px;width:416px;height:416px;border-radius:50%;background:rgba(29,79,156,.88);display:flex;flex-direction:column;align-items:center;justify-content:center;text-align:center;color:var(--white)}
.hero-badge::before{content:"";position:absolute;inset:16px;border:2px solid rgba(255,255,255,.85);border-radius:50%}
.hero-badge h1{font-size:37px;font-weight:600;line-height:1.2;margin-bottom:30px;position:relative}
.btn-light{position:relative;background:var(--blue-soft);color:var(--white);font-size:15px;font-weight:500;padding:9px 24px;border-radius:4px}

.section-title{text-align:center;font-size:35px;font-weight:600}
.divider{display:block;margin:10px auto 0}

.vendors{height:710px;padding-top:82px}
.vendor-grid{display:flex;gap:38px;padding:0 111px;margin-top:40px}
.vendor-card{width:301px;height:354px;border:1px solid #999;border-radius:12px;overflow:hidden;position:relative;text-align:center}
.vendor-photo{height:208px}
.p-taco{background:linear-gradient(135deg,#3a3f48,#8a6a3e 55%,#a9bfd3)}
.p-burger{background:linear-gradient(135deg,#c98a3c,#7a4a22 50%,#d6a35b)}
.p-sweet{background:linear-gradient(135deg,#d9a85e,#f4ede4 60%,#8a2a3a)}
.vendor-name{position:absolute;left:35px;right:35px;top:185px;height:42px;border-radius:10px;background:var(--blue-pill);color:var(--white);font-size:17px;font-weight:500;display:flex;align-items:center;justify-content:center}
.vendor-text{font-size:12.5px;color:var(--muted);line-height:1.45;padding:40px 10px 0}
.vendor-tag{display:flex;align-items:center;justify-content:center;gap:10px;margin-top:14px;font-size:15px;font-weight:500}
.slider-arrows{display:flex;justify-content:center;gap:22px;margin-top:38px}
.arrow{width:39px;height:39px;border-radius:50%;border:1px solid #333;display:flex;align-items:center;justify-content:center}
.arrow.on{background:var(--blue);border-color:var(--blue)}

.bars{height:544px;position:relative;background:linear-gradient(90deg,#1e4a8c,#2d5aa0 45%,#1d4f9c 100%);color:var(--white)}
.bars-copy{position:absolute;left:111px;top:160px;width:440px}
.bars-copy h2{font-size:35px;font-weight:600}
.bars-copy p{font-size:16px;line-height:1.6;margin-top:24px}
.bar-photo{position:absolute;border:3px solid var(--white)}
.bar-one{left:603px;top:87px;width:232px;height:320px;background:linear-gradient(160deg,#1a1530,#5a2a6a 40%,#2b3c8a 70%,#111)}
.bar-two{left:860px;top:144px;width:232px;height:320px;background:linear-gradient(160deg,#3a2412,#b56c2e 45%,#2a1a10)}
.bar-label{position:absolute;bottom:18px;left:30px;background:var(--white);color:var(--blue);font-size:17px;font-weight:500;padding:6px 26px 6px 22px;clip-path:polygon(0 0,92% 0,100% 50%,92% 100%,0 100%);white-space:nowrap}

.testimonials{height:829px;padding-top:100px;position:relative}
.testi-grid{display:flex;gap:41px;padding:0 111px;margin-top:40px}
.testi-card{width:299px;height:295px;border:1px solid #ccc;border-radius:10px;box-shadow:0 0 6px rgba(0,0,0,.15);padding:30px 22px 30px 24px}
.testi-top{display:flex;justify-content:space-between;align-items:center}
.quote{font-size:44px;font-weight:700;line-height:1;height:24px;font-family:Georgia,serif}
.stars{color:var(--star);font-size:13px;letter-spacing:1px}
.testi-card p{font-size:11.8px;color:var(--muted);line-height:1.75;margin-top:26px}
.author{display:flex;align-items:center;gap:14px;margin-top:22px}
.avatar{width:46px;height:46px;border-radius:50%;background:var(--blue);color:var(--white);display:flex;align-items:center;justify-content:center;font-size:16px;flex:none}
.author-name{display:block;font-size:14px;font-weight:500}
.author-role{display:block;font-size:11px;color:#888;margin-top:2px}
.dots{display:flex;justify-content:center;align-items:center;gap:10px;margin-top:38px}
.dots i{width:10px;height:10px;border-radius:50%;background:#555}
.dots i.on{width:14px;height:14px;background:var(--blue)}

.newsletter{position:absolute;left:111px;top:2481px;width:978px;height:278px;background:var(--blue-soft);border-radius:28px;text-align:center;color:var(--white);padding-top:34px;z-index:2}
.newsletter h2{font-size:35px;font-weight:600}
.newsletter p{font-size:16px;line-height:1.6;margin:22px auto 0;width:620px}
.email-field{width:534px;height:44px;margin:22px auto 0;border:1px solid rgba(255,255,255,.85);border-radius:6px;display:flex;align-items:center;justify-content:space-between;padding:0 18px;font-size:14px;color:rgba(255,255,255,.9)}

.site-footer{position:absolute;left:0;top:2685px;width:1200px;height:428px;background:linear-gradient(180deg,#1e4f9a,#1a4890);color:var(--white)}
.foot-links{position:absolute;left:111px;top:136px}
.foot-links h3,.foot-address h3{font-size:21px;font-weight:500}
.link-cols{display:flex;gap:12px;margin-top:14px}
.link-cols ul{list-style:none;width:156px;font-size:15px;line-height:25.7px;white-space:nowrap}
.vsep{position:absolute;top:184px;width:1px;height:96px;background:rgba(255,255,255,.7)}
.foot-brand{position:absolute;left:466px;top:163px;width:295px;height:147px;border:1px solid rgba(255,255,255,.7);text-align:center;padding-top:22px}
.foot-brand::before{content:"";position:absolute;inset:7px;border:1px solid rgba(255,255,255,.5)}
.foot-brand strong{font-size:25px;font-weight:600;position:relative}
.socials{display:flex;justify-content:center;gap:7px;margin-top:10px;position:relative}
.socials span{width:28px;height:28px;border:1.5px solid var(--white);border-radius:50%}
.foot-address{position:absolute;left:850px;top:136px}
.foot-address ul{list-style:none;margin-top:14px;font-size:15px}
.foot-address li{display:flex;align-items:center;gap:18px;height:31px}
.foot-rule{position:absolute;left:0;right:0;top:370px;height:1px;background:rgba(255,255,255,.5)}
.foot-bottom{position:absolute;left:111px;right:111px;top:388px;display:flex;justify-content:space-between;font-size:13px}
</style>
</head>
<body>
<div class="top-strip"></div>
<header class="site-header">
  <a class="brand" href="#">Calloway Food Hall</a>
  <nav class="main-nav">
    <a class="active" href="#">Home</a>
    <a class="has-drop" href="#">Vendors</a>
    <a href="#">Bars</a>
    <a href="#">Patio &amp; Experience</a>
    <a href="#">Events</a>
    <a href="#">Contact Us</a>
  </nav>
</header>

<section class="hero">
  <div class="hero-photo" role="img" aria-label="Bright food hall interior with a white wooden bar counter, copper taps and stools"></div>
  <div class="hero-badge">
    <h1>Coastal Dining<br>Redefined at<br>Calloway Food Hall</h1>
    <a class="btn-light" href="#">Explore Vendors →</a>
  </div>
</section>

<section class="vendors">
  <h2 class="section-title">Our Vendors</h2>
  <svg class="divider" width="100" height="16" viewBox="0 0 100 16"><line x1="8" y1="8" x2="92" y2="8" stroke="#1d4f9c" stroke-width="2"/><circle cx="8" cy="8" r="6" fill="#1d4f9c"/><circle cx="92" cy="8" r="6" fill="#1d4f9c"/></svg>
  <div class="vendor-grid">
    <article class="vendor-card">
      <div class="vendor-photo p-taco" role="img" aria-label="Guest ordering at a taco counter with jars of ingredients"></div>
      <div class="vendor-name">Salt Tide Tacos</div>
      <p class="vendor-text">Lorem ipsum dolor sit amet, consectetur<br>adipiscing elit, sed do eiusmod</p>
      <div class="vendor-tag"><svg width="34" height="30" viewBox="0 0 34 30" fill="none" stroke="#111" stroke-width="1.6"><path d="M3 26a14 14 0 0 1 28 0z"/><path d="M9 12l2-4M17 10V5M25 12l-2-4"/></svg>Tacos &amp; Bowls</div>
    </article>
    <article class="vendor-card">
      <div class="vendor-photo p-burger" role="img" aria-label="Display case of smash burgers"></div>
      <div class="vendor-name">Bluff Burger Co.</div>
      <p class="vendor-text">Lorem ipsum dolor sit amet, consectetur<br>adipiscing elit, sed do eiusmod</p>
      <div class="vendor-tag"><svg width="32" height="30" viewBox="0 0 32 30" fill="none" stroke="#111" stroke-width="1.6"><path d="M3 12a13 9 0 0 1 26 0z"/><path d="M3 16h26M3 20h26"/><path d="M4 24h24a2 2 0 0 1-2 4H6a2 2 0 0 1-2-4z"/></svg>Smash Burgers</div>
    </article>
    <article class="vendor-card">
      <div class="vendor-photo p-sweet" role="img" aria-label="Croissants and a berry-topped cake"></div>
      <div class="vendor-name">Sandpiper Sweets</div>
      <p class="vendor-text">Lorem ipsum dolor sit amet, consectetur<br>adipiscing elit, sed do eiusmod</p>
      <div class="vendor-tag"><svg width="30" height="30" viewBox="0 0 30 30" fill="none" stroke="#111" stroke-width="1.6"><rect x="5" y="14" width="20" height="12"/><path d="M5 18c3 3 6-3 10 0s7 3 10 0"/><path d="M15 4v8"/><path d="M2 27h26"/></svg>Desserts</div>
    </article>
  </div>
  <div class="slider-arrows">
    <a class="arrow" href="#"><svg width="12" height="12" viewBox="0 0 12 12"><path d="M8 2L4 6l4 4" fill="none" stroke="#111" stroke-width="2"/></svg></a>
    <a class="arrow on" href="#"><svg width="12" height="12" viewBox="0 0 12 12"><path d="M4 2l4 4-4 4" fill="none" stroke="#fff" stroke-width="2"/></svg></a>
  </div>
</section>

<section class="bars">
  <div class="bars-copy">
    <h2>Two Bars. Endless Vibes</h2>
    <svg width="170" height="16" viewBox="0 0 170 16" style="margin-top:14px"><line x1="7" y1="8" x2="163" y2="8" stroke="#8fb3e0" stroke-width="2"/><circle cx="7" cy="8" r="6" fill="#8fb3e0"/><circle cx="163" cy="8" r="6" fill="#8fb3e0"/></svg>
    <p>Sed ut perspiciatis unde omnis iste natus error sit voluptatem accusantium doloremque laudantium, totam rem aperiam, eaque ipsa quae ab illo inventore veritatis et quasi architecto beatae vitae dicta sunt explicabo nemo enim ipsam</p>
  </div>
  <div class="bar-photo bar-one" role="img" aria-label="Glowing neon bar sign above bottles"><span class="bar-label">Lantern Bar</span></div>
  <div class="bar-photo bar-two" role="img" aria-label="Row of copper beer taps"><span class="bar-label">The Harbor Tap</span></div>
</section>

<section class="testimonials">
  <h2 class="section-title">Client Testimonials</h2>
  <svg class="divider" width="100" height="16" viewBox="0 0 100 16"><line x1="8" y1="8" x2="92" y2="8" stroke="#1d4f9c" stroke-width="2"/><circle cx="8" cy="8" r="6" fill="#1d4f9c"/><circle cx="92" cy="8" r="6" fill="#1d4f9c"/></svg>
  <div class="testi-grid">
    <article class="testi-card"><div class="testi-top"><span class="quote">&ldquo;</span><span class="stars">★★★★★</span></div><p>Lorem ipsum dolor sit amet, consectetur adipiscing elit, sed do eiusmod tempor incididunt ut labore et dolore magna aliqua. Quis ipsum suspendisse ultrices gravida. Risus commodo viverra maecenas accumsan</p><div class="author"><span class="avatar">DW</span><div><span class="author-name">Dana Whitfield</span><span class="author-role">MD at Harbor Group</span></div></div></article>
    <article class="testi-card"><div class="testi-top"><span class="quote">&ldquo;</span><span class="stars">★★★★★</span></div><p>Lorem ipsum dolor sit amet, consectetur adipiscing elit, sed do eiusmod tempor incididunt ut labore et dolore magna aliqua. Quis ipsum suspendisse ultrices gravida. Risus commodo viverra maecenas accumsan</p><div class="author"><span class="avatar">DW</span><div><span class="author-name">Dana Whitfield</span><span class="author-role">MD at Harbor Group</span></div></div></article>
    <article class="testi-card"><div class="testi-top"><span class="quote">&ldquo;</span><span class="stars">★★★★★</span></div><p>Lorem ipsum dolor sit amet, consectetur adipiscing elit, sed do eiusmod tempor incididunt ut labore et dolore magna aliqua. Quis ipsum suspendisse ultrices gravida. Risus commodo viverra maecenas accumsan</p><div class="author"><span class="avatar">DW</span><div><span class="author-name">Dana Whitfield</span><span class="author-role">MD at Harbor Group</span></div></div></article>
  </div>
  <div class="dots"><i class="on"></i><i></i><i></i><i></i></div>
</section>

<section class="newsletter">
  <h2>Subscribe To Our Newsletter!</h2>
  <svg class="divider" width="190" height="16" viewBox="0 0 190 16"><line x1="8" y1="8" x2="182" y2="8" stroke="#1d4f9c" stroke-width="2"/><circle cx="8" cy="8" r="6" fill="#1d4f9c"/><circle cx="182" cy="8" r="6" fill="#1d4f9c"/></svg>
  <p>Sed ut perspiciatis unde omnis iste natus error sit voluptatem accusantium doloremque laudantium, totam rem aperiam</p>
  <div class="email-field"><span>Enter Your Email Address</span><svg width="18" height="16" viewBox="0 0 18 16"><path d="M1 8L17 1l-4 14-4-5z" fill="#fff"/></svg></div>
</section>

<footer class="site-footer">
  <div class="foot-links">
    <h3>Quick Links</h3>
    <div class="link-cols">
      <ul><li>Home</li><li>Vendors</li><li>Bar</li><li>Patio &amp; Experience</li><li>Events</li><li>Contact Us</li></ul>
      <ul><li>FAQs</li><li>Help Center</li><li>Popular Item</li><li>Special Offer</li></ul>
    </div>
  </div>
  <div class="vsep" style="left:421px"></div>
  <div class="foot-brand">
    <strong>Calloway Food Hall</strong>
    <svg class="divider" width="100" height="16" viewBox="0 0 100 16" style="position:relative"><line x1="8" y1="8" x2="92" y2="8" stroke="#8fb3e0" stroke-width="2"/><circle cx="8" cy="8" r="6" fill="#8fb3e0"/><circle cx="92" cy="8" r="6" fill="#8fb3e0"/></svg>
    <div class="socials" aria-label="Social media links"><span></span><span></span><span></span><span></span><span></span></div>
  </div>
  <div class="vsep" style="left:805px"></div>
  <div class="foot-address">
    <h3>Address Info</h3>
    <ul>
      <li><svg width="16" height="16" viewBox="0 0 16 16"><path d="M3 1l3 3-2 2a9 9 0 0 0 6 6l2-2 3 3-2 2C7 15 1 9 1 3z" fill="#fff"/></svg>+1 8888 - 888 - 888</li>
      <li><svg width="16" height="12" viewBox="0 0 16 12"><rect width="16" height="12" fill="#fff"/><path d="M0 0l8 6 8-6" fill="none" stroke="#1d4f9c" stroke-width="1.5"/></svg>info@callowayfoodhall.com</li>
      <li><svg width="16" height="16" viewBox="0 0 16 16"><path d="M8 1a5 5 0 0 1 5 5c0 4-5 9-5 9S3 10 3 6a5 5 0 0 1 5-5z" fill="#fff"/><circle cx="8" cy="6" r="2" fill="#1d4f9c"/></svg>Seabrook, CA</li>
    </ul>
  </div>
  <div class="foot-rule"></div>
  <div class="foot-bottom">
    <span>© Copyright by Calloway Food Hall - 2025, All Right Reserved.</span>
    <span>Terms &amp; Conditions &nbsp;|&nbsp; Privacy Policy &nbsp;|&nbsp; Sitemaps</span>
  </div>
</footer>
</body>
</html>
```